Business Card Design - Photographer

I am a landscape photographer and I require a business card design. 

I require two designs:
1)  a double sided business card
 and
b)  a single sided business card 

The single sided design can either be the same as the double sided (with just one side having all the information)....or it can be an entire new design. Its up to you.

My corporate colours are (CMYK):

Blue   69, 32, 0, 0
Grey  72,  64,  47,  31
Green  32,  2,  91,  0
Yellow   0, 19, 92, 0
Orange  0, 39, 75, 0

Colour space in final file should be in CMYK.

The details that need to be included on the card:

- Use the provided Logo
- Name: Wiktor Baranowski
- Email:   sales@vistalumeworks.com.au
- Website:    vistalumeworks.com.au
- Twitter:    twitter.com/vistalumeworks
- Facebook:   facebook.com/vistalumeworks
- Mobile  0417 539 662

Please use the attached template to design the logo to the specified size, including the marked bleed lines. I have also attached my logo in PNG (transparent background) and ai format for you to use.

The final file should be:
- Photoshop version with layers so I can edit the name/text etc. All non vector files should be high resolution at 1039 x 697 pixels at 300 dpi.

I also require a file as:
- Vector based PDF

Anyway questions please contact me.

Thank you

Industry/Entity Type

Landscape

Logo styles of interest
Pictorial/Combination Logo
Abstract Logo
Wordmark Logo
Lettermark Logo
Requirements
Must have
• The details that need to be included on the card:

- Use the provided Logo
- Name: Wiktor Baranowski
- Email: sales@vistalumeworks.com.au
- Website: vistalumeworks.com.au
- Twitter: twitter.com/vistalumeworks
- Facebook: facebook.com/vistalumeworks
- Mobile 0417 539 662

```html
<!DOCTYPE html>
<html lang="en">
<head>
<meta charset="utf-8">
<title>Vistalume Works – Business Cards</title>
<link rel="stylesheet" href="https://fonts.googleapis.com/css2?family=Cinzel:wght@400&family=Tinos:wght@400&display=swap">
<style>
  :root {
    --stage: #e8e3dc;
    --card: #ffffff;
    --ink-grey: #3a3c4f;
    --brand-blue: #3f8ccb;
    --text-dark: #2b2b2b;
    --text-light: #ffffff;
    --icon-soft: #cfe3f4;
  }
  * { margin: 0; padding: 0; box-sizing: border-box; }
  html, body { width: 1200px; height: 386px; overflow: hidden; }
  body { background: var(--stage); position: relative; }

  .card {
    position: absolute;
    top: 37px;
    width: 525px;
    height: 300px;
    background: var(--card);
    overflow: hidden;
    box-shadow: 0 2px 6px rgba(0,0,0,0.25);
  }
  .card--front { left: 53px; }
  .card--back  { left: 602px; }

  .card__swoosh { position: absolute; left: 0; top: 0; width: 525px; height: 300px; }
  .swoosh-dark { fill: var(--ink-grey); }
  .swoosh-blue { fill: var(--brand-blue); }

  .brand {
    position: absolute;
    text-align: center;
    color: var(--ink-grey);
    font-family: "Cinzel", serif;
  }
  .card--front .brand { left: 0; width: 320px; top: 36px; }
  .card--back  .brand { left: 0; width: 525px; top: 50px; }

  .brand__mark {
    display: block;
    width: 92px;
    height: 92px;
    margin: 0 auto 12px;
    border-radius: 50%;
    background: var(--ink-grey);
  }
  .brand__name { font-size: 27px; letter-spacing: 0.5px; line-height: 1; }
  .brand__tagline {
    margin-top: 9px;
    font-size: 11px;
    letter-spacing: 1.6px;
    line-height: 1;
  }

  .address {
    position: absolute;
    left: 31px;
    top: 248px;
    font-family: "Tinos", serif;
    font-size: 14px;
    line-height: 18px;
    color: var(--text-dark);
  }

  .contact {
    position: absolute;
    right: 18px;
    top: 192px;
    list-style: none;
    font-family: "Tinos", serif;
    font-size: 14px;
    line-height: 18.5px;
    color: var(--text-light);
    text-align: right;
  }
  .contact li { display: flex; justify-content: flex-end; align-items: center; gap: 4px; }
  .contact svg { width: 9px; height: 9px; fill: var(--icon-soft); flex: none; }
  .contact .icon-square { width: 8px; height: 8px; background: var(--icon-soft); flex: none; }

  .web-address {
    position: absolute;
    left: 0;
    width: 525px;
    top: 253px;
    text-align: center;
    font-family: "Tinos", serif;
    font-size: 13px;
    letter-spacing: 2.4px;
    color: var(--text-dark);
  }
</style>
</head>
<body>

<section class="card card--front">
  <svg class="card__swoosh" viewBox="0 0 525 300" aria-hidden="true">
    <path class="swoosh-dark" d="M455,0 C505,40 510,125 440,170 C370,215 270,262 135,300 L525,300 L525,0 Z"/>
    <path class="swoosh-blue" d="M525,25 C515,105 480,170 405,212 C320,255 230,285 160,300 L525,300 Z"/>
  </svg>

  <div class="brand">
    <span class="brand__mark"></span>
    <div class="brand__name">VISTALUME WORKS</div>
    <div class="brand__tagline">FINE ART PHOTOGRAPHY</div>
  </div>

  <div class="address">
    <p>00, Complex Name</p>
    <p>State Name, City 0020</p>
  </div>

  <ul class="contact">
    <li>
      <svg viewBox="0 0 10 10"><rect x="2.5" y="0" width="5" height="10" rx="1"/></svg>
      0417 539 662
    </li>
    <li><span class="icon-square"></span>vistalumeworks</li>
    <li><span class="icon-square"></span>vistalumeworks</li>
    <li>
      <svg viewBox="0 0 10 10"><rect x="0" y="2" width="10" height="6"/></svg>
      sales@vistalumeworks.com.au
    </li>
    <li>
      <svg viewBox="0 0 10 10"><circle cx="5" cy="5" r="4.5"/></svg>
      www.vistalumeworks.com.au
    </li>
  </ul>
</section>

<section class="card card--back">
  <div class="brand">
    <span class="brand__mark"></span>
    <div class="brand__name">VISTALUME WORKS</div>
    <div class="brand__tagline">FINE ART PHOTOGRAPHY</div>
  </div>
  <p class="web-address">www.vistalumeworks.com.au</p>
</section>

</body>
</html>
```